Gift Cards in the Mail Envelope

Mailing out gift cards in the envelope. Need an eye popping envelope. Please look at the enclosed images. The envelope should look like that.

Low design quality

```html
<!DOCTYPE html>
<html lang="en">
<head>
<meta charset="utf-8">
<title>Gift Card Envelope</title>
<style>
  :root {
    --page-bg: #e4e4e4;
    --envelope-body: #1c1c1c;
    --tone-pink: #d8317e;
    --tone-yellow: #e3d21c;
    --tone-blue: #1414c8;
    --tone-green: #12a628;
    --flap-green: #12a628;
    --window-white: #ffffff;
    --window-border: #0f6f1c;
  }
  html, body {
    margin: 0;
    padding: 0;
    width: 1200px;
    height: 1200px;
    overflow: hidden;
    background: var(--page-bg);
  }
  .canvas {
    position: relative;
    width: 1200px;
    height: 1200px;
  }
  .envelope {
    position: absolute;
    left: 0;
    top: 0;
  }
  .envelope-body {
    fill: var(--envelope-body);
  }
  .pattern-tone {
    opacity: 0.55;
  }
  .pattern-glow {
    opacity: 0.45;
  }
  .address-window {
    fill: var(--window-white);
    stroke: var(--window-border);
    stroke-width: 3;
  }
  .closing-flap {
    fill: var(--flap-green);
  }
</style>
</head>
<body>
<div class="canvas">
  <svg class="envelope" width="1200" height="1200" viewBox="0 0 1200 1200" xmlns="http://www.w3.org/2000/svg">
    <defs>
      <linearGradient id="confetti-tones" x1="0" y1="0" x2="1" y2="0">
        <stop offset="0" stop-color="var(--tone-pink)"/>
        <stop offset="0.33" stop-color="var(--tone-yellow)"/>
        <stop offset="0.66" stop-color="var(--tone-blue)"/>
        <stop offset="1" stop-color="var(--tone-green)"/>
      </linearGradient>
      <radialGradient id="dark-centre" cx="0.5" cy="0.5" r="0.7">
        <stop offset="0" stop-color="var(--envelope-body)" stop-opacity="0.9"/>
        <stop offset="1" stop-color="var(--envelope-body)" stop-opacity="0.2"/>
      </radialGradient>
    </defs>

    <!-- Front of envelope -->
    <g class="envelope-front" role="img" aria-label="Black envelope face covered in a pattern of small pink, yellow, blue and green diamonds">
      <rect class="envelope-body" x="190" y="192" width="818" height="410"/>
      <rect class="pattern-tone" x="190" y="192" width="818" height="410" fill="url(#confetti-tones)"/>
      <rect class="pattern-glow" x="190" y="192" width="818" height="410" fill="url(#dark-centre)"/>
    </g>
    <rect class="address-window" x="265" y="243" width="427" height="174"/>

    <!-- Back of envelope -->
    <g class="envelope-back" role="img" aria-label="Black envelope back covered in a pattern of small pink, yellow, blue and green diamonds">
      <rect class="envelope-body" x="192" y="704" width="814" height="406"/>
      <rect class="pattern-tone" x="192" y="704" width="814" height="406" fill="url(#confetti-tones)"/>
      <rect class="pattern-glow" x="192" y="704" width="814" height="406" fill="url(#dark-centre)"/>
    </g>
    <path class="closing-flap"
          d="M199 704 H1000 V740 Q1000 752 988 758 L606 910 Q600 913 594 911 L212 758 Q199 752 199 740 Z"/>
  </svg>
</div>
</body>
</html>
```